A Vegan Nutritional Supplement (one Product) website

I am looking for an experienced Web designer to build a One Product website for a Nutritional Supplement that is 100% vegan. The emphasis would be on both the Quality and Quantity of the ingredients and their benefits. It contains Essential Vitamins, Minerals, and a proprietary blend of 42 Fruits and Vegetables. I welcome color suggestions as long as it includes Green (vegan) and White.. The final design should communicate to the buyer: Quality, Healthy, Safety (Natural vegan ingredients), Natural energy, well being. The product includes benefits for 3 vital elements of optimal health: Immune Health, Heart Health, and Brain Health

Industry/Entity Type

Health and Wellness - Nutritional Supplements

Number of Pages Required

4 page

Other font styles liked:
• I Welcome your creativity

Colors
59FF00
82FF00
B8FF75
E3FFCB
F4FFEA

Requirements
Must have
• Options to purchase : One product ($34.95); 2 products ($31.45 each - 10% discount), or 3 Products ($27.95 each - 20% discount)
Nice to have
• Focus on the Benefits of having all these Ingredients - Nutrients in one bottle - Essential Vitamins, Minerals, and proprietary blend of 42 Fruits and Vegetables.

```html
<!DOCTYPE html>
<html lang="en">
<head>
<meta charset="utf-8">
<title>Green Vigor – Vegan Nutritional Supplement</title>
<link href="https://fonts.googleapis.com/css2?family=Open+Sans:wght@400;600;700;800&display=swap" rel="stylesheet">
<style>
:root{
  --lime:#59ff00;
  --lime-2:#82ff00;
  --lime-soft:#b8ff75;
  --mint:#e3ffcb;
  --mint-pale:#f4ffea;
  --green-dark:#1d5e22;
  --green-mid:#3d9a2a;
  --green-logo:#3f9a3a;
  --ink:#222;
  --text:#555;
  --footer:#2b2b2b;
  --white:#fff;
}
*{box-sizing:border-box;margin:0;padding:0}
html,body{width:1200px;height:4031px;overflow:hidden}
body{position:relative;font-family:"Open Sans",Arial,sans-serif;color:var(--ink);background:var(--white)}
.abs{position:absolute}

/* top bar + nav */
.promo-bar{left:0;top:0;width:1200px;height:38px;background:var(--footer);color:#fff;font-size:13px;display:flex;align-items:center;justify-content:center;gap:10px}
.nav{left:0;top:38px;width:1200px;height:73px;background:#fff}
.nav a{position:absolute;top:27px;font-size:15px;color:#333;text-decoration:none}
.nav a.active{color:var(--lime-2);color:#5ccf1f}
.btn{display:inline-flex;align-items:center;justify-content:center;background:var(--lime-2);color:var(--green-dark);font-weight:700;border-radius:22px;font-size:15px;text-decoration:none}
.nav .btn{position:absolute;left:917px;top:18px;width:114px;height:38px;color:var(--green-dark)}
.cart{left:1064px;top:62px}
.brand-tab{left:524px;top:38px;width:152px;height:168px;background:var(--green-logo);z-index:5;display:flex;flex-direction:column;align-items:center;justify-content:center;gap:6px}
.brand-tab span{color:#fff;font-weight:800;font-size:26px;line-height:1.05;text-align:center;letter-spacing:.5px}
.brand-dot{width:12px;height:12px;border-radius:50%;background:var(--lime-soft)}

/* hero */
.hero{left:0;top:111px;width:1200px;height:599px;background:linear-gradient(90deg,#2f7a3a 0%,#4e8a4e 35%,#9c8d78 60%,#c7b8a6 100%)}
.hero-title{position:absolute;left:113px;top:168px;font-weight:800;font-size:66px;line-height:1;text-shadow:0 3px 6px rgba(0,0,0,.35)}
.hero-title div{height:86px}
.hero-title .l1{color:#d6ffb0}
.hero-title .l2{color:var(--lime-soft)}
.hero-title .l3{color:var(--lime);height:auto}

/* section headings */
.eyebrow{font-weight:600;font-size:20px;color:var(--ink)}
.heading{font-weight:800;font-size:46px;color:var(--green-dark);letter-spacing:.5px}
.heading em{font-style:normal;color:var(--green-mid)}
.center{left:0;width:1200px;text-align:center}

/* welcome */
.photo{border-radius:0}
.welcome-frame{left:145px;top:819px;width:278px;height:455px;border:2px solid #fff;z-index:2}
.body-text{font-size:16px;line-height:30px;color:var(--text);text-align:justify}

/* benefits */
.benefits{left:0;top:1408px;width:1200px;height:768px;background:var(--mint-pale)}
.benefit h3{font-size:17px;font-weight:700;color:var(--green-dark);line-height:28px}
.benefit p{font-size:16px;line-height:28px;color:var(--text)}
.benefit.left{text-align:right}

/* packages */
.pack{width:294px;height:432px;background:#fff;box-shadow:0 3px 14px rgba(0,0,0,.12);text-align:center}
.pack .bottle{position:absolute;left:84px;top:38px;width:126px;height:228px;border-radius:18px 18px 10px 10px;background:linear-gradient(180deg,#eee 0 16%,#3e8a3e 16% 88%,#2d6a30 88%)}
.pack .badge{position:absolute;left:168px;top:100px;width:88px;height:88px;border-radius:50%;background:#fff;border:3px solid var(--lime-2);display:flex;flex-direction:column;align-items:center;justify-content:center}
.pack .badge b{font-size:26px;font-weight:700;color:#222;line-height:1}
.pack .badge small{font-size:8px;font-weight:700;margin-top:4px}
.pack h4{position:absolute;left:0;width:100%;top:292px;font-size:19px;font-weight:700}
.pack .price{position:absolute;left:0;width:100%;top:321px;font-size:16px;font-weight:700;color:#5ccf1f}
.pack .btn{position:absolute;left:87px;top:351px;width:120px;height:40px}

/* blog */
.blog{left:0;top:2949px;width:1200px;height:715px;background:var(--mint-pale)}
.post{width:472px;height:419px;background:#fff;border:1px solid #ddd}
.post .img{position:absolute;left:0;top:0;width:100%;height:176px}
.post h5{position:absolute;left:18px;top:205px;font-size:17.5px;font-weight:600}
.post p{position:absolute;left:18px;top:248px;width:430px;font-size:15px;line-height:28px;color:var(--text)}
.post svg{position:absolute;left:18px;top:374px}

/* footer */
.footer{left:0;top:3664px;width:1200px;height:367px;background:var(--footer);color:#fff}
.footer h6{position:absolute;font-size:16px;font-weight:700;top:68px}
.footer .rule{position:absolute;top:98px;width:40px;height:2px;background:var(--lime-2)}
.footer ul{position:absolute;top:124px;list-style:none;font-size:14px;line-height:30px}
.footer ul li::before{content:"› ";font-weight:700}
.contact{position:absolute;left:111px;font-size:14px;display:flex;align-items:center;gap:14px}
.social{position:absolute;top:127px;width:30px;height:30px;border-radius:50%;border:1.5px solid #fff}
.subscribe{position:absolute;left:875px;top:253px;width:214px;height:48px;border-radius:24px;background:#fff;color:#888;font-size:14px;padding-left:20px;display:flex;align-items:center}
.subscribe .go{position:absolute;right:5px;top:5px;width:38px;height:38px;border-radius:50%;background:var(--lime-2)}
.copyright{position:absolute;left:0;width:1200px;top:334px;text-align:center;font-size:13px}
</style>
</head>
<body>

<div class="abs promo-bar">50% off on all US orders
  <svg width="16" height="12" viewBox="0 0 16 12"><rect x="1" y="2" width="10" height="7" fill="none" stroke="#fff" stroke-width="1.4"/><path d="M11 4h3l1.5 2.5V9H11z" fill="none" stroke="#fff" stroke-width="1.4"/></svg>
</div>

<nav class="abs nav">
  <a class="active" style="left:113px">Home</a>
  <a style="left:205px">About</a>
  <a style="left:297px">Product</a>
  <a style="left:402px">Reviews</a>
  <a style="left:737px">Blog</a>
  <a style="left:815px">Contact</a>
  <a class="btn">Order Now</a>
</nav>
<svg class="abs cart" width="26" height="24" viewBox="0 0 26 24"><path d="M1 2h4l3 13h13l3-9H7" fill="none" stroke="#333" stroke-width="2"/><circle cx="10" cy="20" r="2" fill="#333"/><circle cx="19" cy="20" r="2" fill="#333"/></svg>

<div class="abs brand-tab">
  <div class="brand-dot"></div>
  <span>GREEN<br>VIGOR</span>
</div>

<section class="abs hero" role="img" aria-label="Smiling woman at a kitchen table holding a supplement bottle, with fruit, milk and breakfast bowls">
  <div class="hero-title">
    <div class="l1">HEART HEALTH</div>
    <div class="l2">BRAIN HEALTH</div>
    <div class="l3">IMMUNE HEALTH</div>
  </div>
</section>

<!-- welcome -->
<div class="abs photo" style="left:111px;top:799px;width:336px;height:468px;background:linear-gradient(160deg,#e8e6e2,#c9b89a 60%,#d8c27a)" role="img" aria-label="Fit woman in a yellow top holding a supplement bottle"></div>
<div class="abs welcome-frame" style="border-left:none;border-bottom:none;left:145px;top:819px"></div>
<div class="abs" style="left:336px;top:1014px;width:158px;height:288px;border-radius:26px 26px 14px 14px;background:linear-gradient(180deg,#f2f2f2 0 20%,#c8ef4a 20% 24%,#3e8a3e 24% 90%,#2d6a30 90%);box-shadow:0 6px 14px rgba(0,0,0,.2);z-index:3" role="img" aria-label="Supplement bottle with green label"></div>
<div class="abs eyebrow" style="left:533px;top:805px">WELCOME TO GREEN VIGOR</div>
<div class="abs heading" style="left:533px;top:838px">GREEN <em>VIGOR</em></div>
<p class="abs body-text" style="left:533px;top:913px;width:557px">Lorem ipsum dolor sit amet, consectetur adipiscing elit, sed do eiusmod tempor incididunt ut labore et dolore magna aliqua. Ut enim ad minnostrud exercitation ullamco laboris nisi ut aliquip ex ea commodo consequat. Duis aute irure dolor in reprehenderit in voluptate velit esse cillum dolore eu fugiat nulla pariatur. Excep teur sint occaecat cupidatat non proident, sunt in culpa qui officia deserunt mollit anim id est laborum.</p>
<p class="abs body-text" style="left:533px;top:1111px;width:557px">Lorem ipsum dolor sit amet, consectetur adipiscing elit, sed do eiusmod tempor incididunt ut labore et dolore magna aliqua. Ut enim ad minnostrud exercitation ullamco laboris nisi ut aliquip ex ea commodo consequat.</p>
<a class="abs btn" style="left:533px;top:1230px;width:119px;height:42px">Learn More</a>

<!-- benefits -->
<section class="abs benefits">
  <div class="abs center eyebrow" style="top:77px">OUR BENEFITS</div>
  <div class="abs center heading" style="top:112px">NUTRIENTS <em>IN ONE BOTTLE</em></div>

  <svg class="abs" style="left:440px;top:300px" width="320" height="260" viewBox="0 0 320 260">
    <polygon points="160,0 320,130 160,260 0,130" fill="var(--lime-soft)" opacity=".7"/>
    <polygon points="160,30 290,130 160,230 30,130" fill="var(--lime-2)" opacity=".8"/>
  </svg>
  <div class="abs" style="left:502px;top:242px;width:191px;height:348px;border-radius:30px 30px 16px 16px;background:linear-gradient(180deg,#f3f3f3 0 20%,#c8ef4a 20% 24%,#3e8a3e 24% 90%,#2d6a30 90%);box-shadow:0 8px 18px rgba(0,0,0,.2)" role="img" aria-label="Supplement bottle with green label"></div>

  <svg class="abs" style="left:354px;top:247px" width="108" height="110" viewBox="0 0 108 110"><path d="M2 2C60 0 108 40 104 108C46 104 4 64 2 2z" fill="#7ccf3a"/><circle cx="58" cy="58" r="14" fill="none" stroke="#fff" stroke-width="3"/></svg>
  <svg class="abs" style="left:354px;top:427px" width="108" height="110" viewBox="0 0 108 110"><path d="M2 2C60 0 108 40 104 108C46 104 4 64 2 2z" fill="#7ccf3a"/><path d="M48 80C44 58 40 46 30 36M48 80C56 60 66 48 78 42" fill="none" stroke="#fff" stroke-width="3"/></svg>
  <svg class="abs" style="left:740px;top:247px" width="108" height="110" viewBox="0 0 108 110"><path d="M106 2C48 0 0 40 4 108C62 104 104 64 106 2z" fill="#7ccf3a"/><rect x="34" y="46" width="40" height="18" rx="9" transform="rotate(-35 54 55)" fill="none" stroke="#fff" stroke-width="3"/></svg>
  <svg class="abs" style="left:740px;top:427px" width="108" height="110" viewBox="0 0 108 110"><path d="M106 2C48 0 0 40 4 108C62 104 104 64 106 2z" fill="#7ccf3a"/><path d="M56 34C46 50 40 58 40 66a16 16 0 0 0 32 0c0-8-6-16-16-32z" fill="none" stroke="#fff" stroke-width="3"/></svg>

  <div class="abs benefit left" style="left:60px;top:243px;width:272px"><h3>PROPRIETARY BLEND OF<br>42 FRUITS &amp; VEGETABLES</h3><p>Lorem ipsum dolor sit ametiq,<br>consectetur adipiscing eli.</p></div>
  <div class="abs benefit left" style="left:60px;top:423px;width:272px"><h3>100% VEGAN</h3><p>Lorem ipsum dolor sit ametiq,<br>consectetur adipiscing eli, sed<br>do eiusmod tempor incidid.</p></div>
  <div class="abs benefit" style="left:868px;top:243px;width:280px"><h3>ESSENTIAL VITAMINS</h3><p>Lorem ipsum dolor sit ametiq,<br>consectetur adipiscing eli, sed<br>do eiusmod tempor incidid.</p></div>
  <div class="abs benefit" style="left:872px;top:423px;width:280px"><h3>MINERALS</h3><p>Lorem ipsum dolor sit ametiq,<br>consectetur adipiscing eli, sed<br>do eiusmod tempor incidid.</p></div>

  <a class="abs btn" style="left:541px;top:657px;width:118px;height:42px">Order Now</a>
</section>

<!-- packages -->
<div class="abs center eyebrow" style="top:2261px">OPTIONS TO PURCHASE</div>
<div class="abs center heading" style="top:2295px">SELECT <em>PACKAGE</em></div>

<div class="abs pack" style="left:111px;top:2434px">
  <div class="bottle" role="img" aria-label="Single supplement bottle"></div>
  <div class="badge"><b>1X</b><small>PACKAGE</small></div>
  <h4>ONE PRODUCT</h4><div class="price">$34.95</div><a class="btn">Add To Cart</a>
</div>
<div class="abs pack" style="left:452px;top:2434px">
  <div class="bottle" role="img" aria-label="Supplement bottle"></div>
  <div class="badge"><b>2X</b><small>10% DISCOUNT</small></div>
  <h4>TWO PRODUCT</h4><div class="price">$31.45 EACH</div><a class="btn">Add To Cart</a>
</div>
<div class="abs pack" style="left:793px;top:2434px">
  <div class="bottle" role="img" aria-label="Supplement bottle"></div>
  <div class="badge"><b>3X</b><small>20% DISCOUNT</small></div>
  <h4>THREE PRODUCT</h4><div class="price">$27.95 EACH</div><a class="btn">Add To Cart</a>
</div>

<!-- blog -->
<section class="abs blog">
  <div class="abs center eyebrow" style="top:66px">LATEST NEWS</div>
  <div class="abs center heading" style="top:100px">OUR <em>BLOG</em></div>
  <article class="abs post" style="left:111px;top:216px">
    <div class="img" style="background:linear-gradient(90deg,#e8b23a,#d9d2c0 40%,#5f8a3a 70%,#3f6a2a)" role="img" aria-label="Woman holding a supplement bottle beside juice and fruit"></div>
    <h5>Lorem ipsum dolor sit amet, co sectetur adipiscing.</h5>
    <p>Sed ut perspiciatis unde omnis iste natus error oluptatem accusantium doloremque laudantium, totam riam, eaque ipsa quae ab illo inventore veritatis et quasito beatae vitae dicta sunt explicabo.</p>
    <svg width="22" height="14" viewBox="0 0 22 14"><path d="M1 7h19M14 1l6 6-6 6" fill="none" stroke="#5ccf1f" stroke-width="2"/></svg>
  </article>
  <article class="abs post" style="left:618px;top:216px">
    <div class="img" style="background:linear-gradient(90deg,#f4f4f4,#d93a2a 25%,#efe9e2 45%,#c6883a 65%,#6f9a3a 85%,#eee)" role="img" aria-label="Heart shape surrounded by healthy fruits, vegetables and fish"></div>
    <h5>Lorem ipsum dolor sit amet, co sectetur adipiscing.</h5>
    <p>Sed ut perspiciatis unde omnis iste natus error oluptatem accusantium doloremque laudantium, totam riam, eaque ipsa quae ab illo inventore veritatis et quasito beatae vitae dicta sunt explicabo.</p>
    <svg width="22" height="14" viewBox="0 0 22 14"><path d="M1 7h19M14 1l6 6-6 6" fill="none" stroke="#5ccf1f" stroke-width="2"/></svg>
  </article>
</section>

<!-- footer -->
<footer class="abs footer">
  <h6 style="left:111px">QUICK LINKS</h6><div class="rule" style="left:111px"></div>
  <div class="contact" style="top:131px"><svg width="14" height="18" viewBox="0 0 14 18"><path d="M7 1a6 6 0 0 1 6 6c0 4-6 10-6 10S1 11 1 7a6 6 0 0 1 6-6z" fill="var(--lime-2)"/><circle cx="7" cy="7" r="2.2" fill="var(--footer)"/></svg><span>Green Vigor</span></div>
  <div class="contact" style="top:156px;left:145px">Address Comes Here</div>
  <div class="contact" style="top:188px"><svg width="16" height="16" viewBox="0 0 16 16"><path d="M3 1l3 3-2 2a10 10 0 0 0 6 6l2-2 3 3-2 2C7 15 1 9 1 3z" fill="var(--lime-2)"/></svg><span>+1 555-010-0199</span></div>
  <div class="contact" style="top:221px"><svg width="16" height="12" viewBox="0 0 16 12"><rect width="16" height="12" fill="var(--lime-2)"/><path d="M0 0l8 6 8-6" fill="none" stroke="var(--footer)" stroke-width="1.5"/></svg><span>hello@greenvigor.com</span></div>

  <h6 style="left:446px">QUICK LINKS</h6><div class="rule" style="left:446px"></div>
  <ul style="left:446px"><li>Home</li><li>About</li><li>Product</li><li>Benefits</li><li>Reviews</li></ul>

  <h6 style="left:660px">SERVICES</h6><div class="rule" style="left:660px"></div>
  <ul style="left:660px"><li>Terms &amp; Conditions</li><li>Privacy Statement</li><li>FAQs</li><li>Blog</li><li>Contact</li></ul>

  <h6 style="left:875px">FOLLOWS</h6><div class="rule" style="left:875px"></div>
  <div class="social" style="left:877px"></div>
  <div class="social" style="left:914px"></div>
  <div class="social" style="left:951px"></div>
  <h6 style="left:875px;top:206px">SUBSCRIBE TO US</h6><div class="rule" style="left:875px;top:236px"></div>
  <div class="subscribe">Email ID<div class="go"><svg width="38" height="38" viewBox="0 0 38 38"><path d="M13 11l14 8-14 8 3-8z" fill="#fff"/></svg></div></div>

  <div class="copyright">2022 Green Vigor. All Rights Reserved.</div>
</footer>

</body>
</html>
```